Modern Verdell Tree Care Website

I need a website for a full service Tree Care company. The company provides tree pruning, tree removal, tree preservation, emergency services, stump grinding, and emergency tree services.

Target Market(s)

Customers that need tree services

Industry/Entity Type

Landscaping, Tree Services

Coding

Coded - Design and coding required

Number of Pages Required

5+ page

Font styles to use
Sans Serif

Requirements
Must have
• Good clean design that showcases the services the company provides.
Nice to have
• Services page; contact form, blog, home page, about page

```html
<!DOCTYPE html>
<html lang="en">
<head>
<meta charset="utf-8">
<title>Verdell Tree Care</title>
<link href="https://fonts.googleapis.com/css2?family=Lexend:wght@400;500;600;700&family=Poppins:wght@400;500;600&display=swap" rel="stylesheet">
<style>
:root{
  --green:#5cc936;
  --green-dark:#2f5d1c;
  --green-soft:#f5fbf0;
  --green-mist:#e6f3dc;
  --brown:#c38a52;
  --ink:#1c1c1c;
  --text:#4a4a4a;
  --night:#262626;
  --white:#fff;
}
*{margin:0;padding:0;box-sizing:border-box}
html,body{width:1200px;height:4669px;overflow:hidden}
body{position:relative;font-family:"Poppins",sans-serif;color:var(--text);background:var(--white)}
.abs{position:absolute}
h1,h2,h3,h4,.brand{font-family:"Lexend",sans-serif;color:var(--ink)}
.brand{font-weight:600;color:var(--green);letter-spacing:1px}
.btn{display:flex;align-items:center;justify-content:center;gap:8px;font-size:13px;font-weight:600;letter-spacing:.5px;color:var(--white);text-transform:uppercase;border-radius:3px}
.btn-brown{background:var(--brown)}
.btn-green{background:var(--green);color:var(--ink)}
.kicker{font-size:15px;font-weight:500;color:var(--green);text-transform:uppercase;letter-spacing:.5px}
.section-title{font-size:40px;font-weight:600}
.brush{height:6px;width:150px;background:var(--green-dark);border-radius:50%}
.center{left:0;width:1200px;text-align:center}
.center .brush{margin:10px auto 0}

/* header */
.topbar{left:700px;top:0;width:500px;height:36px;background:var(--green)}
.topbar-dark{left:0;top:0;width:700px;height:36px;background:var(--night)}
.logo-box{left:72px;top:0;width:270px;height:90px;background:var(--white);display:flex;align-items:center;gap:12px;padding-left:24px}
.logo-box .mark{width:44px;height:44px;background:var(--green);border-radius:4px}
.logo-box .brand{font-size:28px;line-height:1}
.email{left:455px;top:9px;font-size:13px;color:var(--white);display:flex;gap:8px;align-items:center}
.phone{left:768px;top:6px;font-size:19px;font-weight:600;color:var(--ink);display:flex;gap:8px;align-items:center}
.phone small{font-size:11px;font-weight:400}
.nav{left:584px;top:60px;display:flex;gap:38px;align-items:center;font-size:14px;color:var(--ink)}
.nav .active{color:var(--green);border-bottom:3px solid var(--green);padding-bottom:18px;margin-top:21px}
.nav .btn{width:148px;height:48px}

/* hero */
.hero{left:0;top:112px;width:1200px;height:613px;background:linear-gradient(110deg,#3d4a2a 0%,#6b7a4a 40%,#8d9a6a 60%,#52603a 100%)}
.hero h1{position:absolute;top:78px;left:0;width:1200px;text-align:center;font-size:50px;font-weight:700;color:#1c1c1c;letter-spacing:1px}
.hero .btn{position:absolute;left:526px;top:144px;width:148px;height:47px}
.slider{position:absolute;left:490px;top:536px;display:flex;align-items:center;gap:12px;font-size:15px;font-weight:600;color:var(--white)}
.slider .now{color:var(--green)}
.slider .bar{width:160px;height:2px;background:rgba(255,255,255,.5)}
.slider .bar i{display:block;width:30px;height:2px;background:var(--green)}

/* about */
.about-img{left:141px;top:827px;width:377px;height:377px;background:linear-gradient(135deg,#c89a5a,#79a84a 55%,#5a9c32)}
.about-text{left:600px;top:822px;width:488px}
.about-text h2{font-size:38px;font-weight:600;margin:4px 0 10px}
.about-text p{font-size:14.5px;line-height:25px;text-align:justify;margin-top:14px}
.about-text .btn{width:148px;height:46px;margin-top:26px;color:var(--ink)}

/* why */
.why{left:0;top:1323px;width:1200px;height:825px;background:var(--green-soft)}
.why-title{top:1410px}
.feature{font-family:"Lexend",sans-serif;font-size:21px;font-weight:500;color:var(--ink);line-height:22px}
.feature.r{text-align:right}
.hub{left:459px;top:1577px;width:308px;height:308px;border-radius:50%;background:var(--green);display:flex;flex-direction:column;align-items:center;justify-content:center;box-shadow:0 0 0 8px var(--white),0 0 0 10px var(--green)}
.hub .brand{color:var(--white);font-size:38px}
.hub .sub{color:var(--white);font-size:18px;letter-spacing:6px;font-family:"Lexend",sans-serif}

/* services */
.services{left:0;top:2148px;width:1200px;height:725px;background:var(--green)}
.services .kicker,.services h2{color:var(--white)}
.services-title{top:2230px}
.card{top:2355px;width:300px;height:437px;background:var(--white);border-radius:10px;overflow:hidden;text-align:center}
.card .photo{height:248px;background:linear-gradient(135deg,#55703a,#8aa660 50%,#3f5a2a)}
.card h3{font-size:30px;font-weight:600;margin:24px 0 12px}
.card p{font-size:12.5px;line-height:19px;padding:0 18px}
.arrow{top:2562px;width:50px;height:50px;border-radius:50%;background:var(--white);border:2px solid var(--green-dark);display:flex;align-items:center;justify-content:center}

/* blog */
.blog-title{top:2955px}
.blog-feature{left:83px;top:3064px;width:488px;height:431px;background:linear-gradient(160deg,#3f6e2a,#7fae4a 55%,#b9d08a)}
.blog-overlay{left:112px;top:3383px;width:490px;height:156px;background:#111;border-radius:6px;padding:30px 34px;color:var(--white)}
.meta{font-size:11px;display:flex;gap:20px}
.blog-overlay h4{color:#e2a15f;font-size:17px;font-weight:500;margin:12px 0 6px}
.blog-overlay p{font-size:12px;line-height:19px}
.post{left:622px;width:473px;height:127px;background:var(--white);border-radius:6px;box-shadow:0 3px 14px rgba(0,0,0,.12);display:flex;overflow:hidden}
.post .thumb{width:170px;height:127px;background:linear-gradient(135deg,#5a4a2a,#9a7a3a 50%,#4a6a2a)}
.post .body{padding:14px 18px;width:303px}
.post .meta{color:var(--ink);font-size:10.5px;gap:30px}
.post h4{font-size:16px;font-weight:500;line-height:20px;margin:8px 0 6px}
.post p{font-size:10px;line-height:15px}
.view-more{left:526px;top:3559px;width:148px;height:47px;color:var(--ink)}

/* contact */
.contact{left:0;top:3698px;width:1200px;height:590px;background:var(--green-mist)}
.contact-title{top:3800px}
.contact-intro{left:112px;top:3925px;width:405px;font-size:15px;line-height:25px}
.reach{left:112px;display:flex;gap:12px;align-items:center}
.reach .ico{width:46px;height:46px;border-radius:50%;background:var(--green);display:flex;align-items:center;justify-content:center}
.reach small{font-size:11px;display:block}
.reach span{font-size:14px;color:var(--ink);line-height:20px}
.field{background:var(--ink);color:#ddd;font-size:13px;padding:12px 18px}
.send{left:542px;top:4164px;width:169px;height:44px;color:var(--ink)}

/* footer */
.footer{left:0;top:4288px;width:1200px;height:381px;background:var(--night)}
.foot-logo{left:127px;top:4440px;display:flex;gap:14px;align-items:center}
.foot-logo .mark{width:60px;height:60px;background:var(--green);border-radius:4px}
.foot-logo .brand{font-size:40px}
.col h4{color:var(--white);font-size:18px;font-weight:600;padding-bottom:10px;border-bottom:1px solid #555;width:fit-content;margin-bottom:14px}
.col a{display:block;color:#ccc;font-size:12px;line-height:24px;text-decoration:none}
.rule{left:112px;top:4590px;width:976px;height:1px;background:#555}
.copy{left:0;top:4622px;width:1200px;text-align:center;color:#ddd;font-size:13px}
</style>
</head>
<body>

<!-- header -->
<div class="abs topbar-dark"></div>
<div class="abs topbar"></div>
<div class="abs logo-box"><span class="mark"></span><span class="brand">VERDELL</span></div>
<div class="abs email">
  <svg width="20" height="20" viewBox="0 0 20 20"><circle cx="10" cy="10" r="10" fill="#c38a52"/><path d="M5 7h10v7H5z M5 7l5 4 5-4" fill="none" stroke="#fff" stroke-width="1.2"/></svg>
  Email: info@verdelltreecare.com
</div>
<div class="abs phone">
  <svg width="24" height="24" viewBox="0 0 24 24"><circle cx="12" cy="12" r="12" fill="#1c1c1c"/><path d="M8 7c1-1 2 0 2.5 1.5S10 10 10 10c.6 1.5 2.3 3.4 4 4 0 0 .8-1 1.5-.6S17 15 16.5 16c-.6 1.2-2.5 1.3-4.5 0S7.4 11.6 7.2 9.6C7 8.5 7.5 7.5 8 7z" fill="#fff"/></svg>
  <small>CALL US</small> (555) 214-3870 &nbsp;|&nbsp; (555) 639-1024
</div>
<nav class="abs nav">
  <span class="active">Home</span><span>About Us</span><span>Our Services</span><span>Blog</span>
  <span class="btn btn-brown">Contact Us ›</span>
</nav>

<!-- hero -->
<section class="abs hero" role="img" aria-label="Arborist in safety gear cutting a fallen pine with a chainsaw in a forest">
  <h1>VERDELL TREE CARE</h1>
  <span class="btn btn-brown">Contact Us ›</span>
  <div class="slider"><span class="now">01</span><span class="bar"><i></i></span><span>05</span></div>
</section>

<!-- about -->
<div class="abs about-img" role="img" aria-label="Collage of tree service work: cut timber, crew at work and green grass"></div>
<div class="abs about-text">
  <div class="kicker">Welcome To</div>
  <h2>Verdell Tree Care</h2>
  <div class="brush"></div>
  <p>At Verdell Tree Care, we are more than just a tree service company, we are stewards of our beautiful trees. With a passion deeply rooted in arboriculture, we embark on a mission to promote the health, beauty, and safety of your trees and landscapes.</p>
  <p>Whether it's expert tree trimming to enhance aesthetics, meticulous tree removal to mitigate hazards, or comprehensive tree health assessments to ensure safety, we approach each task with unwavering dedication and attention to detail.</p>
  <span class="btn btn-green" style="display:inline-flex">Learn More ›</span>
</div>

<!-- why choose us -->
<section class="abs why"></section>
<div class="abs center why-title"><div class="kicker">Our Excellence</div><h2 class="section-title">Why Choose Us</h2><div class="brush"></div></div>
<svg class="abs" style="left:0;top:0" width="1200" height="2148" viewBox="0 0 1200 2148">
  <path d="M448 1570 A232 232 0 1 0 787 1570" fill="none" stroke="#9a9a9a" stroke-width="1.5"/>
  <g fill="#fff" stroke="#5cc936" stroke-width="2.5">
    <circle cx="448" cy="1570" r="10"/><circle cx="787" cy="1570" r="10"/>
    <circle cx="383" cy="1715" r="10"/><circle cx="852" cy="1715" r="10"/>
    <circle cx="433" cy="1880" r="10"/><circle cx="801" cy="1880" r="10"/>
    <circle cx="613" cy="1967" r="10"/>
  </g>
</svg>
<div class="abs feature r" style="right:787px;top:1545px">Licensed and<br>Insured</div>
<div class="abs feature" style="left:843px;top:1545px">Professional<br>Work</div>
<div class="abs feature r" style="right:846px;top:1692px">24-Hours Emergency<br>Services</div>
<div class="abs feature" style="left:884px;top:1700px">Safety is<br>Our No.1 Priority</div>
<div class="abs feature r" style="right:796px;top:1862px">Locally Owned &amp;<br>Operated</div>
<div class="abs feature" style="left:834px;top:1868px">Free<br>Estimates</div>
<div class="abs feature" style="left:413px;width:420px;text-align:center;top:1990px">Licensed Arborist<br>on Staff</div>
<div class="abs hub"><span class="brand">VERDELL</span><span class="sub">TREE CARE</span></div>

<!-- services -->
<section class="abs services"></section>
<div class="abs center services-title"><div class="kicker">Our Services</div><h2 class="section-title">What We Do</h2></div>
<article class="abs card" style="left:112px"><div class="photo" role="img" aria-label="Climber in harness trimming branches of a tall tree"></div><h3>Tree Trimming</h3><p>Karspiciatis unde omnis iste natus error sit voluptatem accusantium doloremque laudantium, totam rem aperiam, eaque ipsa quae ab illo inventore</p></article>
<article class="abs card" style="left:450px"><div class="photo" role="img" aria-label="Chainsaw cutting a stump on the forest floor"></div><h3>Tree Removal</h3><p>Karspiciatis unde omnis iste natus error sit voluptatem accusantium doloremque laudantium, totam rem aperiam, eaque ipsa quae ab illo inventore</p></article>
<article class="abs card" style="left:789px"><div class="photo" role="img" aria-label="Worker clearing undergrowth with a chainsaw"></div><h3>Tree Clearing</h3><p>Karspiciatis unde omnis iste natus error sit voluptatem accusantium doloremque laudantium, totam rem aperiam, eaque ipsa quae ab illo inventore</p></article>
<div class="abs arrow" style="left:25px"><svg width="14" height="14" viewBox="0 0 14 14"><path d="M9 2 4 7l5 5" fill="none" stroke="#1c1c1c" stroke-width="2"/></svg></div>
<div class="abs arrow" style="left:1124px"><svg width="14" height="14" viewBox="0 0 14 14"><path d="M5 2l5 5-5 5" fill="none" stroke="#1c1c1c" stroke-width="2"/></svg></div>

<!-- blog -->
<div class="abs center blog-title"><div class="kicker">Blog</div><h2 class="section-title">Latest Blog</h2><div class="brush"></div></div>
<div class="abs blog-feature" role="img" aria-label="Gardener in gloves pruning a branch with red loppers"></div>
<div class="abs blog-overlay">
  <div class="meta"><span>BY ADMIN</span><span>|</span><span>MAY 12, 2024</span></div>
  <h4>Perspiciatis unde omnis iste natus error sit.</h4>
  <p>Saerspiciatis unde omnis iste natus error sit voluptatem accusan tium doloremque laudantiumotam rem aperiameaque.</p>
</div>
<article class="abs post" style="top:3062px"><div class="thumb" role="img" aria-label="Arborist in a sunlit forest"></div><div class="body"><div class="meta"><span>By Admin</span><span>May 12, 2024</span></div><h4>Perspiciatis unde omnis iste natus error sit.</h4><p>Saerspiciatis unde omnis iste natus error sit voluptatem accusan tium.</p></div></article>
<article class="abs post" style="top:3216px"><div class="thumb" role="img" aria-label="Worker felling a large tree trunk"></div><div class="body"><div class="meta"><span>By Admin</span><span>May 12, 2024</span></div><h4>Perspiciatis unde omnis iste natus error sit.</h4><p>Saerspiciatis unde omnis iste natus error sit voluptatem accusan tium.</p></div></article>
<article class="abs post" style="top:3369px"><div class="thumb" role="img" aria-label="Chainsaw cutting through a log with sawdust"></div><div class="body"><div class="meta"><span>By Admin</span><span>May 12, 2024</span></div><h4>Perspiciatis unde omnis iste natus error sit.</h4><p>Saerspiciatis unde omnis iste natus error sit voluptatem accusan tium.</p></div></article>
<span class="abs btn btn-green view-more">View More ›</span>

<!-- contact -->
<section class="abs contact"></section>
<div class="abs center contact-title"><div class="kicker">Get In Touch</div><h2 class="section-title">Contact Us</h2><div class="brush"></div></div>
<p class="abs contact-intro">Karspiciatis unde omnis istasesae natus erseror sisest voluptatem accusantium doseaselor saeseemqseue laudantium, totam rem aperiam, eaque ipsa quae ab illo inventore.</p>
<div class="abs reach" style="top:4038px"><span class="ico"><svg width="20" height="20" viewBox="0 0 24 24"><path d="M6 3c1.5-1 3 0 3.6 2.2S8.8 7.8 8.8 7.8c.9 2.2 3.4 5 5.9 5.9 0 0 1.2-1.5 2.2-.9s2.3 2.1 1.6 3.6c-.9 1.8-3.7 1.9-6.6 0S4.2 11.3 4 8.4C3.8 6.8 4.9 4 6 3z" fill="#fff"/></svg></span><div><small>Call Us</small><span>(555) 214-3870<br>(555) 639-1024</span></div></div>
<div class="abs reach" style="top:4121px"><span class="ico"><svg width="20" height="20" viewBox="0 0 20 20"><path d="M3 5h14v10H3z M3 5l7 6 7-6" fill="none" stroke="#fff" stroke-width="1.6"/></svg></span><div><small>Email</small><span>info@verdelltreecare.com</span></div></div>
<div class="abs field" style="left:542px;top:3907px;width:546px;height:42px">Your Name *</div>
<div class="abs field" style="left:542px;top:3967px;width:262px;height:41px">Email *</div>
<div class="abs field" style="left:826px;top:3967px;width:262px;height:41px">Phone Number *</div>
<div class="abs field" style="left:542px;top:4027px;width:546px;height:125px">Enter Your Message *</div>
<span class="abs btn btn-green send">Send Message ›</span>

<!-- footer -->
<footer class="abs footer"></footer>
<div class="abs foot-logo"><span class="mark"></span><span class="brand">VERDELL</span></div>
<div class="abs col" style="left:517px;top:4374px"><h4>Quick Links</h4><a>Home</a><a>About Us</a><a>Our Services</a><a>Blog</a><a>Contact Us</a></div>
<div class="abs col" style="left:711px;top:4374px"><h4>Links</h4><a>Copyright</a><a>Terms of Use</a><a>Privacy Policy</a><a>Accessibility</a><a>Sitemap</a></div>
<div class="abs col" style="left:888px;top:4374px"><h4>Support</h4><a>Team</a><a>About Us</a><a>Careers</a><a>Our Values</a></div>
<div class="abs rule"></div>
<div class="abs copy">©2024. All rights reserved.</div>

</body>
</html>
```